Brookmere Osteopathy flyer

I want a clean clear DL flyer (but also want an A4 poster) promoting a new Osteopathic business in a semi rural area in Tasmania (Australia).
It can have pictures like the examples attached to show people what Osteopathy is (its like Chiropractic and physiotherapy).
I am the sole practioner and am male, so any pictures would be best to be a white male if possible.
I've attached some wording, you can use all, or none of it
I don't have a phone number for the business yet
info@brookmereosteopathy.example
www.brookmereosteopathy.example
Target Market(s)
Australians, from tradies, professionals, babies to retired people
Industry/Entity Type
Health
Look and feel

```html
<!DOCTYPE html>
<html lang="en">
<head>
<meta charset="utf-8">
<title>Brookmere Osteopathy Flyer</title>
<link rel="stylesheet" href="https://fonts.googleapis.com/css2?family=Montserrat:wght@500;600;700&family=Poppins:ital,wght@1,800;1,900&display=swap">
<style>
  :root {
    --orange: #f0914a;
    --orange-deep: #e8823a;
    --blue: #1e9ad6;
    --white: #ffffff;
    --skin-light: #f6ece6;
    --skin: #e9d6cc;
    --hex-border: #fbf8f4;
  }
  * { margin: 0; padding: 0; box-sizing: border-box; }
  html, body { width: 897px; height: 1200px; overflow: hidden; background: #444; }
  .flyer {
    position: relative;
    width: 897px;
    height: 1200px;
    background: var(--orange);
    overflow: hidden;
    font-family: "Montserrat", sans-serif;
    color: var(--white);
  }
  .hero-photo {
    position: absolute;
    left: 0; top: 0;
    width: 897px; height: 640px;
    border-radius: 0 0 140px 140px;
    background: linear-gradient(180deg, #ffffff 0%, #fbf6f3 30%, var(--skin-light) 60%, var(--skin) 100%);
  }
  .brand-mark {
    position: absolute;
    left: 338px; top: 48px;
    width: 220px; height: 220px;
    border: 2px solid var(--blue);
    border-radius: 50%;
    display: flex; align-items: center; justify-content: center;
    text-align: center;
  }
  .brand-mark span {
    font-family: "Montserrat", sans-serif;
    font-weight: 600;
    font-size: 19px;
    letter-spacing: 2px;
    color: var(--blue);
    line-height: 1.3;
  }
  .headline {
    position: absolute;
    left: 0; width: 897px; top: 300px;
    text-align: center;
    font-family: "Poppins", sans-serif;
    font-style: italic;
    font-weight: 900;
    font-size: 84px;
    line-height: 76px;
    letter-spacing: -4px;
  }
  .headline .line-one { color: var(--orange); display: block; }
  .headline .line-two { color: var(--blue); display: block; }
  .service-photos {
    position: absolute;
    left: 0; top: 490px;
    width: 897px; height: 260px;
  }
  .service-photo { position: absolute; top: 0; }
  .reasons-title {
    position: absolute;
    left: 0; width: 897px; top: 770px;
    text-align: center;
    font-family: "Poppins", sans-serif;
    font-style: italic;
    font-weight: 800;
    font-size: 31px;
    letter-spacing: -1px;
  }
  .reasons-list {
    position: absolute;
    top: 837px;
    list-style: none;
    border-top: 2px dashed rgba(255,255,255,0.9);
    border-left: 2px dashed rgba(255,255,255,0.9);
    padding: 6px 0 4px 12px;
    font-size: 17px;
    font-weight: 500;
  }
  .reasons-list.left { left: 75px; width: 330px; }
  .reasons-list.right { left: 460px; width: 330px; }
  .reasons-list li {
    display: flex; align-items: center; gap: 8px;
    height: 24px; white-space: nowrap;
  }
  .reasons-list svg { flex: none; }
  .about-text {
    position: absolute;
    left: 60px; width: 777px; top: 985px;
    text-align: center;
    font-size: 13.2px;
    font-weight: 500;
    line-height: 24px;
  }
  .contact-band {
    position: absolute;
    left: 0; top: 1081px;
    width: 897px; height: 119px;
    background: var(--blue);
  }
  .contact-list {
    position: absolute;
    left: 56px; top: 20px;
    list-style: none;
    font-size: 18px;
    font-weight: 500;
  }
  .contact-list li {
    display: flex; align-items: center; gap: 12px;
    height: 24px;
  }
  .call-to-action {
    position: absolute;
    right: 66px; top: 22px;
    text-align: right;
  }
  .call-to-action .prompt {
    display: block;
    font-size: 26px;
    font-weight: 600;
    line-height: 28px;
  }
  .call-to-action .phone {
    display: block;
    font-family: "Montserrat", sans-serif;
    font-size: 38px;
    font-weight: 700;
    letter-spacing: 1px;
    line-height: 42px;
  }
</style>
</head>
<body>
<main class="flyer">
  <div class="hero-photo" role="img" aria-label="Photo of an osteopath treating a patient's back and shoulder on a treatment table"></div>

  <div class="brand-mark"><span>BROOKMERE<br>OSTEOPATHY</span></div>

  <h1 class="headline">
    <span class="line-one">BROOKMERE</span>
    <span class="line-two">OSTEOPATHY</span>
  </h1>

  <div class="service-photos">
    <svg class="service-photo" style="left:90px" width="234" height="260" viewBox="0 0 234 260" role="img" aria-label="Photo of hands treating a patient's lower back">
      <defs><linearGradient id="g1" x1="0" y1="0" x2="0" y2="1"><stop offset="0" stop-color="#f1e4dc"/><stop offset="1" stop-color="#c9a590"/></linearGradient></defs>
      <polygon points="117,12 222,70 222,190 117,248 12,190 12,70" fill="url(#g1)" stroke="var(--hex-border)" stroke-width="10" stroke-linejoin="round"/>
    </svg>
    <svg class="service-photo" style="left:331px" width="234" height="260" viewBox="0 0 234 260" role="img" aria-label="Photo of hands gently cradling a sleeping baby's head">
      <defs><linearGradient id="g2" x1="0" y1="0" x2="0" y2="1"><stop offset="0" stop-color="#e4e0ea"/><stop offset="1" stop-color="#5fa8cf"/></linearGradient></defs>
      <polygon points="117,12 222,70 222,190 117,248 12,190 12,70" fill="url(#g2)" stroke="var(--hex-border)" stroke-width="10" stroke-linejoin="round"/>
    </svg>
    <svg class="service-photo" style="left:573px" width="234" height="260" viewBox="0 0 234 260" role="img" aria-label="Photo of a practitioner treating a woman's head and neck">
      <defs><linearGradient id="g3" x1="0" y1="0" x2="0" y2="1"><stop offset="0" stop-color="#eef0f4"/><stop offset="1" stop-color="#b8a49a"/></linearGradient></defs>
      <polygon points="117,12 222,70 222,190 117,248 12,190 12,70" fill="url(#g3)" stroke="var(--hex-border)" stroke-width="10" stroke-linejoin="round"/>
    </svg>
  </div>

  <h2 class="reasons-title">Common Reasons People Visit An Osteopath:</h2>

  <ul class="reasons-list left">
    <li><svg width="15" height="15" viewBox="0 0 16 16"><circle cx="8" cy="8" r="6.5" fill="none" stroke="#fff" stroke-width="1.6"/><path d="M4.5 8l2.5 2.5L15 2.5" fill="none" stroke="#fff" stroke-width="1.8"/></svg>Back / neck pain</li>
    <li><svg width="15" height="15" viewBox="0 0 16 16"><circle cx="8" cy="8" r="6.5" fill="none" stroke="#fff" stroke-width="1.6"/><path d="M4.5 8l2.5 2.5L15 2.5" fill="none" stroke="#fff" stroke-width="1.8"/></svg>Headaches / migraines</li>
    <li><svg width="15" height="15" viewBox="0 0 16 16"><circle cx="8" cy="8" r="6.5" fill="none" stroke="#fff" stroke-width="1.6"/><path d="M4.5 8l2.5 2.5L15 2.5" fill="none" stroke="#fff" stroke-width="1.8"/></svg>Joint and muscle pain</li>
    <li><svg width="15" height="15" viewBox="0 0 16 16"><circle cx="8" cy="8" r="6.5" fill="none" stroke="#fff" stroke-width="1.6"/><path d="M4.5 8l2.5 2.5L15 2.5" fill="none" stroke="#fff" stroke-width="1.8"/></svg>Pregnancy-related discomfort</li>
    <li><svg width="15" height="15" viewBox="0 0 16 16"><circle cx="8" cy="8" r="6.5" fill="none" stroke="#fff" stroke-width="1.6"/><path d="M4.5 8l2.5 2.5L15 2.5" fill="none" stroke="#fff" stroke-width="1.8"/></svg>Disc related issues</li>
  </ul>

  <ul class="reasons-list right">
    <li><svg width="15" height="15" viewBox="0 0 16 16"><circle cx="8" cy="8" r="6.5" fill="none" stroke="#fff" stroke-width="1.6"/><path d="M4.5 8l2.5 2.5L15 2.5" fill="none" stroke="#fff" stroke-width="1.8"/></svg>Sciatica</li>
    <li><svg width="15" height="15" viewBox="0 0 16 16"><circle cx="8" cy="8" r="6.5" fill="none" stroke="#fff" stroke-width="1.6"/><path d="M4.5 8l2.5 2.5L15 2.5" fill="none" stroke="#fff" stroke-width="1.8"/></svg>Plantar fasciitis</li>
    <li><svg width="15" height="15" viewBox="0 0 16 16"><circle cx="8" cy="8" r="6.5" fill="none" stroke="#fff" stroke-width="1.6"/><path d="M4.5 8l2.5 2.5L15 2.5" fill="none" stroke="#fff" stroke-width="1.8"/></svg>Tendonitis / Bursitis</li>
    <li><svg width="15" height="15" viewBox="0 0 16 16"><circle cx="8" cy="8" r="6.5" fill="none" stroke="#fff" stroke-width="1.6"/><path d="M4.5 8l2.5 2.5L15 2.5" fill="none" stroke="#fff" stroke-width="1.8"/></svg>Adhesive capsulitis (frozen shoulder)</li>
    <li><svg width="15" height="15" viewBox="0 0 16 16"><circle cx="8" cy="8" r="6.5" fill="none" stroke="#fff" stroke-width="1.6"/><path d="M4.5 8l2.5 2.5L15 2.5" fill="none" stroke="#fff" stroke-width="1.8"/></svg>Tennis / Golfers elbow</li>
  </ul>

  <p class="about-text">Osteopaths use a combination of joint manipulation, targeted deep tissue massage and stretching<br>to improve function, relieve pain and support the body’s ability to heal itself.</p>

  <footer class="contact-band">
    <ul class="contact-list">
      <li><svg width="16" height="18" viewBox="0 0 16 18"><path d="M8 17s6-6 6-10.5A6 6 0 0 0 2 6.5C2 11 8 17 8 17z" fill="none" stroke="#fff" stroke-width="1.4"/><circle cx="8" cy="6.5" r="2" fill="none" stroke="#fff" stroke-width="1.4"/></svg>48 Ridgeline Road, Brookmere</li>
      <li><svg width="17" height="17" viewBox="0 0 18 18"><circle cx="9" cy="9" r="7.5" fill="none" stroke="#fff" stroke-width="1.3"/><ellipse cx="9" cy="9" rx="3.2" ry="7.5" fill="none" stroke="#fff" stroke-width="1.3"/><path d="M1.5 9h15" stroke="#fff" stroke-width="1.3"/></svg>www.brookmereosteopathy.example</li>
      <li><svg width="17" height="14" viewBox="0 0 18 14"><rect x="1" y="1" width="16" height="12" rx="1.5" fill="none" stroke="#fff" stroke-width="1.3"/><path d="M1.5 2l7.5 6 7.5-6" fill="none" stroke="#fff" stroke-width="1.3"/></svg>info@brookmereosteopathy.example</li>
    </ul>
    <div class="call-to-action">
      <span class="prompt">CALL US NOW!</span>
      <span class="phone">555-014-2200</span>
    </div>
  </footer>
</main>
</body>
</html>
```